Upmarket Label for a new product: Pecan Oil

I require a label for a Pecan Oil Bottle 750ml similar to a wine bottle.
Our company is Halvard. You'll find our logo in the attachments.
Refer to this file: File 6: halvard_logobig white tuesday, 15 september 2015 09:41:037
I have attached pictures of the bottle we will be using. The label is however not ours but one of our customers.
At the top on the bottle neck I need an emboss label similar to the example.
I have also attached our own label and packaging as a reference.
Please include the Nutritional info in the design.
The text to be included in the design can be found in this file:
Target Market(s)
-Health Market with a LSM of 7 and up.
-Main retail stores
-End users
Industry/Entity Type
Retail
Requirements
Must have
- -Picture of a pecan
- -The HALVARD logo
- - Nutritional Information - provided in attached file
- - Bottle is green. Keep that in mind
- - Emboss logo on the bottle neck
- - Reference on the front to " Cholesterol Free"
Should not have
- - Pictures of other types of nuts

```html
<!DOCTYPE html>
<html lang="en">
<head>
<meta charset="utf-8">
<title>Halvard Pecan Oil Label</title>
<link rel="stylesheet" href="https://fonts.googleapis.com/css2?family=Pinyon+Script&family=Cormorant+Garamond:wght@500;600&display=swap">
<style>
  :root {
    --backdrop: #eef0ef;
    --label-paper: #ffffff;
    --label-edge: #d9dbd8;
    --cocoa: #4a2c1e;
    --cocoa-soft: #6b4a38;
    --muted-grey: #8a8a86;
    --nut-light: #c98a5a;
    --nut-dark: #7a4426;
    --leaf: #7da857;
  }
  * { margin: 0; padding: 0; box-sizing: border-box; }
  html, body {
    width: 849px;
    height: 1200px;
    overflow: hidden;
    background: var(--backdrop);
  }
  .canvas {
    position: relative;
    width: 849px;
    height: 1200px;
    font-family: "Cormorant Garamond", serif;
  }
  .neck-label {
    position: absolute;
    left: 50%;
    top: 90px;
    transform: translateX(-50%);
    width: 220px;
    height: 120px;
    border-radius: 50%;
    background: var(--cocoa);
    display: flex;
    align-items: center;
    justify-content: center;
  }
  .neck-label .brand-name {
    color: var(--label-paper);
    font-size: 40px;
    font-weight: 600;
    letter-spacing: 1px;
  }
  .front-label {
    position: absolute;
    left: 114px;
    top: 290px;
    width: 620px;
    height: 780px;
    background: var(--label-paper);
    border: 1px solid var(--label-edge);
    box-shadow: 0 2px 10px rgba(0,0,0,0.06);
    text-align: center;
  }
  .front-label .brand-badge {
    position: absolute;
    left: 50%;
    top: 48px;
    transform: translateX(-50%);
    display: flex;
    align-items: center;
    gap: 10px;
  }
  .brand-badge .badge-square {
    width: 18px;
    height: 18px;
    background: var(--cocoa);
  }
  .brand-badge .brand-name {
    color: var(--cocoa);
    font-size: 34px;
    font-weight: 600;
    letter-spacing: 1px;
  }
  .product-title {
    position: absolute;
    left: 0;
    right: 0;
    top: 150px;
    font-family: "Pinyon Script", cursive;
    font-size: 128px;
    line-height: 1;
    color: var(--cocoa);
    font-weight: 400;
  }
  .product-claim {
    position: absolute;
    left: 0;
    right: 0;
    top: 312px;
    font-size: 24px;
    font-weight: 500;
    letter-spacing: 6px;
    color: var(--muted-grey);
  }
  .pecan-art {
    position: absolute;
    left: 100px;
    top: 380px;
    width: 420px;
    height: 300px;
  }
</style>
</head>
<body>
  <main class="canvas">
    <div class="neck-label">
      <span class="brand-name">halvard</span>
    </div>

    <section class="front-label">
      <div class="brand-badge">
        <span class="badge-square"></span>
        <span class="brand-name">halvard</span>
      </div>
      <h1 class="product-title">Pecan Oil</h1>
      <p class="product-claim">CHOLESTEROL FREE</p>
      <svg class="pecan-art" viewBox="0 0 420 300" role="img" aria-label="Illustration of whole and shelled pecan nuts with green leaves">
        <defs>
          <radialGradient id="pecan-tone" cx="50%" cy="50%" r="55%">
            <stop offset="0%" stop-color="var(--nut-light)"/>
            <stop offset="70%" stop-color="var(--nut-dark)"/>
            <stop offset="100%" stop-color="var(--nut-dark)" stop-opacity="0"/>
          </radialGradient>
          <radialGradient id="leaf-tone" cx="50%" cy="50%" r="50%">
            <stop offset="0%" stop-color="var(--leaf)" stop-opacity="0.7"/>
            <stop offset="100%" stop-color="var(--leaf)" stop-opacity="0"/>
          </radialGradient>
        </defs>
        <ellipse cx="90" cy="150" rx="70" ry="60" fill="url(#leaf-tone)"/>
        <ellipse cx="220" cy="155" rx="190" ry="130" fill="url(#pecan-tone)"/>
      </svg>
    </section>
  </main>
</body>
</html>
```